Velmora Consulting Business

** Please add the content information from my old business card
1. I would like to see a two sided business card with both options with the 1st Option--Tallow Spire-new WHITE BACKGROUND LOGO
2 nd Option-Tallow Spire - new BLACK- Background Logo
3rd -Option a business card with my Photo on the card
Please add the new word to the card information:
EXECUTION
AS THE OWNER'S REP
WE AIM TO ACHIEVE YOUR
INFRASTRUCTURE VISION with
OUR SPECIALIZATION & EXECUTION in:

FUNDING Planning
BUSINESS Planning
INFRASTRUCTURE Planning
PROJECT Management
Since 2012
_____________________________________________________________________
I want to get spot uv raised printing. I was liking a a nice rich white linen paper stock with black writing & NOT A COLORED CARD other than a variety of white or black cards concept

```html
<!DOCTYPE html>
<html lang="en">
<head>
<meta charset="utf-8">
<title>Velmora Consulting – Business Card</title>
<link rel="stylesheet" href="https://fonts.googleapis.com/css2?family=Roboto:wght@400;700&display=swap">
<style>
  :root {
    --page: #e9e8e6;
    --card-black: #141414;
    --card-white: #ffffff;
    --ink: #1a1a1a;
    --accent: #dc1838;
    --gloss: #4a4a4a;
    --back-text: #f2f2f2;
    --photo-top: #c98a4e;
    --photo-bottom: #1d1d1d;
  }
  * { margin: 0; padding: 0; box-sizing: border-box; }
  html, body { width: 1200px; height: 960px; overflow: hidden; }
  body {
    background: var(--page);
    font-family: "Roboto", Arial, sans-serif;
    display: flex;
    flex-direction: column;
    align-items: center;
    justify-content: center;
    gap: 40px;
  }
  .card {
    width: 760px;
    height: 434px;
    border-radius: 26px;
    position: relative;
    overflow: hidden;
    box-shadow: 0 6px 18px rgba(0,0,0,0.18);
  }
  /* Back side */
  .card-back {
    background: var(--card-black);
    color: var(--back-text);
    display: flex;
    flex-direction: column;
    align-items: center;
    justify-content: center;
    text-align: center;
  }
  .brand-back {
    display: flex;
    flex-direction: column;
    align-items: center;
    margin-bottom: 34px;
  }
  .brand-back .brand-name {
    font-size: 62px;
    font-weight: 700;
    color: var(--gloss);
    line-height: 1;
  }
  .brand-back .brand-sub {
    font-size: 15px;
    letter-spacing: 14px;
    color: var(--gloss);
    margin-top: 8px;
    margin-right: -14px;
    text-transform: uppercase;
  }
  .tagline {
    font-size: 19px;
    line-height: 1.35;
    max-width: 560px;
  }
  .rule {
    width: 60px;
    height: 1px;
    background: var(--back-text);
    margin: 14px auto;
  }
  .services {
    font-size: 19px;
    line-height: 1.4;
    max-width: 620px;
  }
  .services .dot {
    display: inline-block;
    width: 7px; height: 7px;
    background: var(--back-text);
    margin: 0 8px 3px;
    vertical-align: middle;
  }
  /* Front side */
  .card-front { background: var(--card-white); color: var(--ink); }
  .front-info {
    position: absolute;
    left: 56px;
    top: 54px;
  }
  .brand-front { display: flex; align-items: center; gap: 12px; margin-bottom: 30px; }
  .brand-front .mark {
    width: 18px; height: 18px; background: var(--ink);
  }
  .brand-front .brand-name {
    font-size: 44px; font-weight: 700; line-height: 1; color: var(--ink);
  }
  .brand-front .brand-sub {
    display: block;
    font-size: 12px; letter-spacing: 11px; text-transform: uppercase; margin-top: 6px;
  }
  .person-name { font-size: 27px; font-weight: 700; }
  .person-title {
    font-size: 16px; color: var(--accent); text-transform: uppercase; margin: 4px 0 20px;
  }
  .contact { font-size: 19px; line-height: 1.45; }
  .locations { margin-top: 8px; font-size: 19px; }
  .locations .sep {
    display: inline-block; width: 7px; height: 7px; border-radius: 50%;
    background: var(--accent); margin: 0 8px 3px; vertical-align: middle;
  }
  .portrait {
    position: absolute;
    right: 40px;
    bottom: 0;
    width: 270px;
    height: 360px;
    border-radius: 130px 130px 0 0;
    background: linear-gradient(180deg, var(--photo-top) 0%, #8c6a56 30%, var(--photo-bottom) 60%);
  }
</style>
</head>
<body>
  <section class="card card-back">
    <div class="brand-back">
      <span class="brand-name">Velmora</span>
      <span class="brand-sub">Consulting</span>
    </div>
    <p class="tagline">As the Owner’s Rep we aim to achieve your infrastructure vision with our Specialization &amp; Execution in</p>
    <div class="rule"></div>
    <p class="services">
      Funding Planning<span class="dot"></span>Business Planning<span class="dot"></span>Infrastructure Planning<br>
      <span class="dot"></span>Project Management Since 2012
    </p>
  </section>

  <section class="card card-front">
    <div class="front-info">
      <div class="brand-front">
        <span class="mark"></span>
        <div>
          <span class="brand-name">Velmora</span>
          <span class="brand-sub">Consulting</span>
        </div>
      </div>
      <h1 class="person-name">Marianne Holt-Devereaux</h1>
      <p class="person-title">CEO / Lead Project Manager</p>
      <p class="contact">867.555.0172<br>marianne@velmora.ca | www.velmora.ca</p>
      <p class="locations">Coldwater NT<span class="sep"></span>Riverton NB</p>
    </div>
    <div class="portrait" role="img" aria-label="Portrait photo of the card holder, arms crossed, in a black top"></div>
  </section>
</body>
</html>
```